Meridale Partners Website

Meridale Partners (MP) provide Analytics & Enterprise Performance Management (EPM) advisory & consultancy services. We are passionate about data and making a difference for our clients by working in partnership with them, helping them on their journey to becoming an Meridale Partner. We deliver insights which give our clients a competitive edge and a much deeper understanding of their organisation.

We need a website which shows who we are, what we do and how we do it.

www.meridale-partners.example is our very basic website at the moment. We want to completely revamp it with a corporate look

```html
<!DOCTYPE html>
<html lang="en">
<head>
<meta charset="utf-8">
<title>Meridale Partners</title>
<link rel="stylesheet" href="https://fonts.googleapis.com/css2?family=Montserrat:wght@400;500;600;700;800;900&family=Poppins:wght@400;500;600&display=swap">
<style>
:root{
  --blue:#3c69b0;
  --blue-dark:#2c5597;
  --gold:#c28b45;
  --gold-light:#d8ad72;
  --brown:#7a4e2d;
  --ink:#222;
  --grey:#8a8a8a;
  --paper:#ffffff;
  --footer:#f2f3f5;
}
*{box-sizing:border-box;margin:0;padding:0}
html,body{width:1200px;height:2601px;overflow:hidden}
body{position:relative;font-family:"Montserrat",sans-serif;color:var(--ink);background:var(--paper)}

/* header */
.site-header{position:absolute;left:0;top:0;width:1200px;height:80px;background:var(--paper);z-index:2}
.brand{position:absolute;display:flex;align-items:center;justify-content:center;gap:8px;background:var(--blue);color:#fff;font-weight:700;font-size:11px;letter-spacing:.5px;line-height:1.2}
.brand .dot{width:20px;height:20px;border-radius:50%;border:3px solid #fff;flex:none}
.site-header .brand{left:93px;top:8px;width:160px;height:72px}
.nav{position:absolute;width:610px;height:16px;font-family:"Poppins",sans-serif;font-size:12px;font-weight:500;color:#222}
.nav span{position:absolute;top:0;white-space:nowrap;line-height:16px}
.nav .sep{top:6px;width:16px;height:4px;background:var(--blue)}
.site-header .nav{left:286px;top:32px}
.search{position:absolute;border:1px solid #cfd3da;background:#fff;font-size:10px;color:#333;display:flex;align-items:center;padding-left:11px}
.search svg{position:absolute;right:10px;top:50%;transform:translateY(-50%)}

/* backdrop */
.backdrop{position:absolute;left:0;top:80px;width:1200px;height:2332px;
  background:linear-gradient(180deg,#2b65c9 0%,#5a8ed6 10%,#93abc8 20%,#a7a39c 27%,#9a7a55 34%,#9a6a3e 42%,#6a4a35 52%,#3e3c42 66%,#2e2e34 85%,#2b2a30 100%)}

/* hero */
.hero-frame{position:absolute;left:92px;top:204px;width:1015px;height:307px;border:1px solid rgba(190,215,255,.8);background:rgba(80,130,220,.12)}
.hero-title{position:absolute;left:0;top:304px;width:1200px;text-align:center;color:#fff;font-weight:900;font-size:60px;letter-spacing:2px}
.hero-sub{position:absolute;left:0;top:374px;width:1200px;text-align:center;color:#fff;font-weight:600;font-size:23px;letter-spacing:.5px}
.hero-btn{position:absolute;left:436px;top:472px;width:329px;height:80px;background:#fff;border-top:5px solid var(--blue);color:var(--blue);font-weight:700;font-size:18px;display:flex;align-items:center;justify-content:center;box-shadow:0 6px 16px rgba(0,0,0,.15)}

/* profile */
.profile{position:absolute;left:92px;top:697px;width:373px;height:996px;background:#fff}
.profile-frame{position:absolute;left:47px;top:30px;width:280px;height:390px;border:3px solid var(--gold)}
.portrait{position:absolute;left:74px;top:57px;width:225px;height:211px;background:linear-gradient(160deg,#7b6a5e,#3d3330 60%,#1f1c1f)}
.profile-namebg{position:absolute;left:32px;top:282px;width:310px;height:96px;background:#fff}
.profile-name{position:absolute;left:0;top:285px;width:373px;text-align:center;color:var(--gold);font-weight:800;font-size:37px}
.profile-role{position:absolute;left:0;top:333px;width:373px;text-align:center;font-size:16px;font-weight:500}
.signature{position:absolute;left:77px;top:362px;width:220px;height:42px;background:linear-gradient(90deg,#e9e4dc,#d9d1c4)}
.live-band{position:absolute;left:0;top:452px;width:373px;height:122px;background:linear-gradient(90deg,#c49252,#e2c090);color:#fff;font-weight:700;font-size:35px;line-height:45px;padding:18px 0 0 28px}
.profile-text{position:absolute;left:29px;top:596px;width:315px;font-family:"Poppins",sans-serif;font-size:12px;line-height:24.5px;color:var(--grey);text-align:justify}
.profile-text p+p{margin-top:24px}
.blue-bar{position:absolute;left:29px;top:881px;width:61px;height:8px;background:var(--blue)}
.full-btn{position:absolute;left:0;top:923px;width:154px;height:45px;background:var(--gold);color:#fff;font-size:11px;font-weight:700;display:flex;align-items:center}
.full-btn .arrow{width:44px;height:45px;background:rgba(255,255,255,.15);display:flex;align-items:center;justify-content:center;margin-right:16px}

/* project cards */
.card{position:absolute;width:193px;height:400px;background:#fff}
.card .photo{position:absolute;left:0;top:0;width:193px;height:181px}
.card .cat{position:absolute;left:14px;top:193px;color:var(--gold);font-size:11.5px;font-weight:500}
.card h3{position:absolute;left:13px;top:211px;font-size:17px;font-weight:700;color:#1f1f1f}
.card .desc{position:absolute;left:14px;top:238px;width:166px;font-size:8.1px;line-height:18.4px;color:#8a8a8a;text-align:justify;text-transform:uppercase}
.card .more{position:absolute;left:0;bottom:0;width:193px;height:42px;font-size:10.5px;font-weight:700;color:#fff;display:flex;align-items:center;padding-left:14px;gap:6px}
.card .more i{width:13px;height:13px;border:1px solid #fff;border-radius:50%;display:inline-block}
.row1 .more{background:rgba(120,80,45,.8)}
.row2 .more{background:rgba(60,60,66,.85)}

/* feature */
.feature{position:absolute;left:496px;top:1114px;width:611px;height:295px;border:1px solid var(--gold)}
.feature-copy{position:absolute;left:0;top:0;width:269px;height:293px;background:linear-gradient(90deg,#8a5c33,#6e4a30);color:#fff}
.feature-copy .kicker{position:absolute;left:17px;top:30px;font-size:11.5px;font-weight:500}
.feature-copy .rule{position:absolute;left:17px;top:55px;width:32px;height:3px;background:#fff}
.feature-copy h2{position:absolute;left:17px;top:68px;font-size:29px;line-height:37px;font-weight:700}
.feature-copy p{position:absolute;left:17px;top:148px;width:222px;font-size:8.4px;line-height:18.5px;font-weight:500}
.feature-copy .go{position:absolute;left:17px;top:237px;width:24px;height:24px;background:#fff;display:flex;align-items:center;justify-content:center}
.feature-photo{position:absolute;left:269px;top:0;width:340px;height:293px;background:linear-gradient(180deg,#6fa5dd,#b9cfe4 40%,#4d7d6a 75%,#2f5a36)}

/* award */
.award{position:absolute;left:92px;top:1888px;width:1015px;height:462px;background:linear-gradient(100deg,#1f3e7c,#b8632c 45%,#e08a3a 60%,#3a2a40)}
.award-card{position:absolute;left:56px;top:65px;width:570px;height:332px;background:#fff}
.award-photo{position:absolute;left:0;top:0;width:84px;height:332px;background:linear-gradient(180deg,#4c6b70,#2c3d42 60%,#1d2427)}
.award-go{position:absolute;left:84px;top:109px;width:40px;height:39px;background:var(--blue);display:flex;align-items:center;justify-content:center}
.award-card .kicker{position:absolute;left:143px;top:52px;color:var(--blue);font-size:15.5px;font-weight:500}
.award-card .rule{position:absolute;left:143px;top:78px;width:28px;height:3px;background:#222}
.award-card h2{position:absolute;left:141px;top:86px;color:var(--gold);font-size:47px;font-weight:800}
.award-card h4{position:absolute;left:142px;top:148px;font-size:20.5px;font-weight:500}
.award-card p{position:absolute;left:142px;top:175px;width:398px;color:var(--blue);font-size:10px;line-height:24.6px;text-align:justify;text-transform:uppercase}

/* footer */
.site-footer{position:absolute;left:0;top:2412px;width:1200px;height:189px;background:var(--footer)}
.footer-base{position:absolute;left:0;top:2575px;width:1200px;height:26px;background:#dedfe2}
.footer-logo{position:absolute;left:507px;top:2385px;width:185px;height:95px;background:#fff;border-top:3px solid var(--gold);padding:6px;box-shadow:0 4px 12px rgba(0,0,0,.12)}
.footer-logo .brand{position:static;width:100%;height:100%}
.site-footer .nav{left:299px;top:92px}
</style>
</head>
<body>

<header class="site-header">
  <div class="brand"><span class="dot"></span><span>MERIDALE<br>PARTNERS</span></div>
  <nav class="nav"><span style="left:0">HOME</span><span class="sep" style="left:69px"></span><span style="left:118px">ABOUT US</span><span class="sep" style="left:211px"></span><span style="left:259px">SERVICE</span><span class="sep" style="left:339px"></span><span style="left:390px">PUBLICATION</span><span class="sep" style="left:495px"></span><span style="left:549px">CAREERS</span></nav>
  <div class="search" style="left:924px;top:24px;width:183px;height:35px">SEARCH
    <svg width="12" height="12" viewBox="0 0 12 12"><circle cx="5" cy="5" r="4" fill="none" stroke="#3c69b0" stroke-width="1.4"/><path d="M8 8l3 3" stroke="#3c69b0" stroke-width="1.4"/></svg></div>
</header>

<div class="backdrop" role="img" aria-label="Photo of sky with clouds behind a modern glass office building"></div>

<section>
  <div class="hero-frame"></div>
  <h1 class="hero-title">MERIDALE PARTNERS</h1>
  <p class="hero-sub">ATA ANALYTICS &amp; EPM CONSULTING SERVICES</p>
  <div class="hero-btn">VANTOR &amp; ASSOCIATES</div>
</section>

<aside class="profile">
  <div class="profile-frame"></div>
  <div class="portrait" role="img" aria-label="Portrait photo of the founder"></div>
  <div class="profile-namebg"></div>
  <div class="profile-name">ELENA MARSH</div>
  <div class="profile-role">FOUNDER</div>
  <div class="signature" role="img" aria-label="Handwritten signature"></div>
  <div class="live-band">LIVE<br>BETTER</div>
  <div class="profile-text">
    <p>Lorem ipsum dolor sit amet, consectetur adipiscing elit, sed do eiusmod tempor incididunt ut labore et dolore magna aliqua. Quis ipsum suspendisse ultrices gravida. Risus commodo viverra maecenas accumsan lacus lacus vel facilisis</p>
    <p>adipiscing elit, sed do eiusmod tempor incididunt ut labore et dolore magna aliqua. Quis ipsum suspendisse ultrices gravida. Risus commodo viverra maecenas accumsan lacu</p>
  </div>
  <div class="blue-bar"></div>
  <div class="full-btn"><span class="arrow"><svg width="10" height="16" viewBox="0 0 10 16"><path d="M2 2l6 6-6 6" fill="none" stroke="#fff" stroke-width="2"/></svg></span>FULL ARTICAL</div>
</aside>

<section class="row1">
  <article class="card" style="left:496px;top:697px">
    <div class="photo" role="img" aria-label="Stone villa with pool at sunset" style="background:linear-gradient(180deg,#8b7aa0,#c9a27a 55%,#7c8c94)"></div>
    <span class="cat">ARCHITECTURE</span><h3>CAVE RESIDENCE</h3>
    <p class="desc">Lorem ipsum dolor sit amet, consectetur adipiscing elit, sed do eiusmod tempor incididunt ut consectetur adipiscing elit, sed do eiusmod tempor incididunt ut v lacus vel facilisis.</p>
    <div class="more">LEARN MORE <i></i></div>
  </article>
  <article class="card" style="left:705px;top:697px">
    <div class="photo" role="img" aria-label="White modern kitchen interior" style="background:linear-gradient(180deg,#f2f2f2,#d9d9d9 60%,#b5b5b5)"></div>
    <span class="cat">INTERIOR</span><h3>VIGA COTTAGE</h3>
    <p class="desc">Lorem ipsum dolor sit amet, consectetur adipiscing elit, sed do eiusmod tempor incididunt ut consectetur adipiscing elit, sed do eiusmod tempor incididunt ut v lacus vel facilisis.</p>
    <div class="more">LEARN MORE <i></i></div>
  </article>
  <article class="card" style="left:914px;top:697px">
    <div class="photo" role="img" aria-label="Modern house with pool and lawn" style="background:linear-gradient(180deg,#6aa6e0,#d9d4cc 50%,#5c9a45)"></div>
    <span class="cat">LANDSCAPE</span><h3>GRASS HOUSE</h3>
    <p class="desc">Lorem ipsum dolor sit amet, consectetur adipiscing elit, sed do eiusmod tempor incididunt ut consectetur adipiscing elit, sed do eiusmod tempor incididunt ut v lacus vel facilisis.</p>
    <div class="more">LEARN MORE <i></i></div>
  </article>
</section>

<section class="feature">
  <div class="feature-copy">
    <span class="kicker">CORVELL UNIVERSITY</span>
    <span class="rule"></span>
    <h2>COMMUNITY<br>CENTER</h2>
    <p>Lorem ipsum dolor sit amet, consectetur adipiscing elit, sed do eiusmod tempor incididunt ut labore et dolore magna a maecenas accumsan lacus vel facilisis maecenas accumsan lacus.</p>
    <span class="go"><svg width="8" height="12" viewBox="0 0 8 12"><path d="M2 1l5 5-5 5" fill="none" stroke="#6e4a30" stroke-width="1.6"/></svg></span>
  </div>
  <div class="feature-photo" role="img" aria-label="Glass towers rising above green trees"></div>
</section>

<section class="row2">
  <article class="card" style="left:496px;top:1426px">
    <div class="photo" role="img" aria-label="Timber house lit at dusk" style="background:linear-gradient(180deg,#2b4569,#5a4a3c 60%,#2a2a2a)"></div>
    <span class="cat">ARCHITECTURE</span><h3>CAVE RESIDENCE</h3>
    <p class="desc">Lorem ipsum dolor sit amet, consectetur adipiscing elit, sed do eiusmod tempor incididunt ut consectetur adipiscing elit, sed do eiusmod tempor incididunt ut v lacus vel facilisis.</p>
    <div class="more">LEARN MORE <i></i></div>
  </article>
  <article class="card" style="left:705px;top:1426px">
    <div class="photo" role="img" aria-label="White farmhouse under grey sky" style="background:linear-gradient(180deg,#8a9196,#c5c8c9 50%,#2f3b2e)"></div>
    <span class="cat">INTERIOR</span><h3>VIGA COTTAGE</h3>
    <p class="desc">Lorem ipsum dolor sit amet, consectetur adipiscing elit, sed do eiusmod tempor incididunt ut consectetur adipiscing elit, sed do eiusmod tempor incididunt ut v lacus vel facilisis.</p>
    <div class="more">LEARN MORE <i></i></div>
  </article>
  <article class="card" style="left:914px;top:1426px">
    <div class="photo" role="img" aria-label="Brick house at night" style="background:linear-gradient(180deg,#2f4a66,#3a3532 60%,#1f1e1e)"></div>
    <span class="cat">LANDSCAPE</span><h3>GRASS HOUSE</h3>
    <p class="desc">Lorem ipsum dolor sit amet, consectetur adipiscing elit, sed do eiusmod tempor incididunt ut consectetur adipiscing elit, sed do eiusmod tempor incididunt ut v lacus vel facilisis.</p>
    <div class="more">LEARN MORE <i></i></div>
  </article>
</section>

<section class="award" role="img" aria-label="Restaurant table with a glass of red wine and a hand holding a phone">
  <div class="award-card">
    <div class="award-photo" role="img" aria-label="Dark glass skyscraper"></div>
    <span class="award-go"><svg width="10" height="16" viewBox="0 0 10 16"><path d="M2 2l6 6-6 6" fill="none" stroke="#fff" stroke-width="2"/></svg></span>
    <span class="kicker">AWARD</span>
    <span class="rule"></span>
    <h2>HALDEN</h2>
    <h4>RIVERSIDE RESTAURANT</h4>
    <p>Lorem ipsum dolor sit amet, consectetur adipiscing elit, sed do eiusmod tempor incididunt ut labore et dolore magna aliqua. Quis ipsum suspendisse ultrices gravida. Risus commodo viverra maecenas accumsan lacus vel facilisis.Lorem ipsum dolor sit suspendisse ultrices gravida. Risus commodo viverr</p>
  </div>
</section>

<footer class="site-footer">
  <nav class="nav"><span style="left:0">HOME</span><span class="sep" style="left:69px"></span><span style="left:118px">ABOUT US</span><span class="sep" style="left:211px"></span><span style="left:259px">SERVICE</span><span class="sep" style="left:339px"></span><span style="left:390px">PUBLICATION</span><span class="sep" style="left:495px"></span><span style="left:549px">CAREERS</span></nav>
</footer>
<div class="footer-base"></div>
<div class="footer-logo"><div class="brand"><span class="dot"></span><span>MERIDALE<br>PARTNERS</span></div></div>
<div class="search" style="left:507px;top:2545px;width:185px;height:35px">SEARCH
  <svg width="12" height="12" viewBox="0 0 12 12"><circle cx="5" cy="5" r="4" fill="none" stroke="#3c69b0" stroke-width="1.4"/><path d="M8 8l3 3" stroke="#3c69b0" stroke-width="1.4"/></svg></div>

</body>
</html>
```